Wordpress website re-design

Update existing 5 page wordpress website to look more professional. We run a 10 week boxing program that ends in a black tie gala event.

We would like to keep the existing pink hero colour.

The website:
- must be Wordpress
- prefer it to work with the PageBuilder plugin for easy future changes
- Keep the existing URL structure
- Use white space/backgrounds - D not want all black background or the pink colour used as the background for an entire section
- Shouldn't look too 'templatey'. Good flow between sections

Logo, images and video to use can be found here: https://files.qorvanshare.net/folders/8kq3ZtLmWpe2RxvBn7HsYcDa4-Tu?usp=sharing

Website to be redesigned: https://punchforpurpose-example.com.au/

Target Market(s)

Men working office jobs aged 28-38

Coding

Coded - Design and coding required

Number of Pages Required

5+ page

Colors

Designer to choose colors to be used in the design.

Requirements
Must have
• Wordpress
Nice to have
• Work with PageBuilder so that I can easily make changes in the future
Should not have
• Entirely black background. Want it to be lighter / plenty of white background. Not too blocky - flowing through sections and some of the images with backgrounds removed to make it less blocky also. I do not want it to be clerly 'templatey'. The pink should be used as a hero colour, not for entire sections

```html
<!DOCTYPE html>
<html lang="en">
<head>
<meta charset="utf-8">
<title>Contact – Punch For Purpose</title>
<link rel="stylesheet" href="https://fonts.googleapis.com/css2?family=Oswald:wght@500;600;700&family=Roboto:wght@400;500&family=Jost:wght@400;500&display=swap">
<style>
:root{
  --pink:#f0036c;
  --ink:#000;
  --dark:#131313;
  --admin:#1d2327;
  --white:#fff;
  --muted:#c9c9c9;
  --map-green:#cfe6c4;
  --map-blue:#a9cbe8;
}
*{box-sizing:border-box;margin:0;padding:0}
html,body{width:1200px;height:2585px;overflow:hidden}
body{position:relative;background:var(--white);font-family:Roboto,sans-serif;color:var(--white)}
.abs{position:absolute}

.admin-bar{left:0;top:0;width:1200px;height:30px;background:var(--admin);font-size:13px;color:#dcdcde;display:flex;align-items:center;padding:0 12px;gap:22px}
.admin-bar .right{margin-left:auto}

.hero{left:0;top:30px;width:1200px;height:720px;background:radial-gradient(ellipse at 72% 38%,#5a2a2a 0%,#2a1616 30%,#101010 65%,#070707 100%)}
.topline{left:0;top:30px;width:1200px;height:48px;border-bottom:1px solid rgba(255,255,255,.12);font-size:14px}
.topline .ask{left:57px;top:15px;display:flex;align-items:center;gap:12px}
.dot{width:10px;height:10px;border:2px solid var(--pink);border-radius:50%}
.sq{width:14px;height:14px;background:var(--white);border-radius:3px;display:inline-block}
.topline .social{right:60px;top:16px;display:flex;gap:26px}

.brand{font-family:Oswald,sans-serif;font-weight:700;color:var(--white);text-transform:uppercase;line-height:.95;display:flex;align-items:center;gap:10px}
.brand .mark{width:14px;height:14px;background:var(--pink)}
.header-brand{left:57px;top:100px;font-size:30px;width:160px}
.nav{left:287px;top:134px;display:flex;gap:47px;font-family:Oswald,sans-serif;font-weight:600;font-size:14px;letter-spacing:.6px}
.join{left:1022px;top:121px;width:118px;height:43px;background:var(--pink);font-family:Oswald,sans-serif;font-weight:500;font-size:16px;display:flex;align-items:center;justify-content:center;letter-spacing:.5px}

.hero-kicker{left:57px;top:344px;font-family:Oswald,sans-serif;font-weight:600;font-size:25px;color:var(--pink)}
.hero-title{left:57px;top:390px;font-family:Oswald,sans-serif;font-weight:600;font-size:51px;line-height:54px;letter-spacing:.5px}
.crumbs{left:983px;top:411px;font-family:Oswald,sans-serif;font-weight:600;font-size:17px;display:flex;gap:18px;align-items:center;letter-spacing:.5px}
.crumbs .sep{color:var(--pink);font-size:14px}

.map{background:linear-gradient(135deg,var(--map-green),#e6efd9 40%,#d6e8c8 70%,var(--map-blue))}
.big-map{left:47px;top:1075px;width:1104px;height:468px}

.contact-info{left:65px;top:833px;width:535px;height:387px;background:var(--ink);padding:46px 45px}
.contact-info .label{font-size:12px;color:#2a2a2a}
.contact-info h2{font-family:Jost,sans-serif;font-weight:500;font-size:31px;line-height:30px;margin:6px 0 24px}
.contact-info p{font-size:15px;margin-bottom:20px}
.contact-info .icons{display:flex;gap:8px;margin-top:4px}
.contact-info .icons span{width:28px;height:27px;background:var(--pink);display:flex;align-items:center;justify-content:center}

.contact-form{left:600px;top:833px;width:535px;height:387px;background:var(--pink);padding:42px 45px}
.contact-form h3{font-family:Jost,sans-serif;font-weight:500;font-size:28px;margin-bottom:12px}
.field{width:445px;height:38px;background:var(--white);border-radius:19px;margin-bottom:19px;color:#9a9a9a;font-size:13px;padding:11px 15px}
.field.msg{height:82px;border-radius:24px;padding-top:7px}
.send{width:445px;height:38px;background:var(--white);color:var(--pink);font-size:15px;display:flex;align-items:center;justify-content:center}

.cta{left:0;top:1560px;width:1200px;height:580px;background:radial-gradient(ellipse at 55% 70%,#3a2a24 0%,#1a1512 45%,#0b0b0b 100%)}
.cta-kicker{left:0;top:1797px;width:1200px;text-align:center;font-family:Roboto,sans-serif;font-weight:500;font-size:23px;letter-spacing:1.5px;color:var(--pink)}
.cta-title{left:0;top:1840px;width:1200px;text-align:center;font-family:Oswald,sans-serif;font-weight:600;font-size:49px;line-height:55px}
.cta-btn{left:531px;top:1988px;width:138px;height:43px;background:var(--pink);font-family:Oswald,sans-serif;font-weight:600;font-size:15px;display:flex;align-items:center;justify-content:center;letter-spacing:.5px}

.footer{left:0;top:2138px;width:1200px;height:447px;background:var(--dark)}
.footer-brand{left:47px;top:2215px;font-size:44px;width:220px}
.footer h4{font-family:Oswald,sans-serif;font-weight:600;font-size:19px;letter-spacing:.5px}
.links{left:425px;top:2213px}
.links ul{list-style:none;margin-top:18px}
.links li{font-size:15px;color:#ddd;margin-bottom:18px;display:flex;gap:13px}
.links li::before{content:"›";color:var(--pink);font-weight:500}
.training{left:793px;top:2213px;width:357px}
.training .addr{display:flex;gap:10px;font-size:15px;color:#ddd;margin-top:18px;line-height:23px}
.small-map{left:793px;top:2313px;width:358px;height:124px}
.rule{left:47px;top:2512px;width:1104px;height:1px;background:#2c2c2c}
.copy{left:47px;top:2536px;font-size:13px;color:#ddd}
.foot-social{left:1018px;top:2531px;display:flex;gap:18px}
.foot-social span{width:28px;height:28px;border-radius:50%;background:var(--pink);display:flex;align-items:center;justify-content:center}
.foot-social i{width:10px;height:10px;background:var(--white);border-radius:2px}
</style>
</head>
<body>

<div class="abs admin-bar">
  <span>Ringside</span><span>Customize</span><span>1</span><span>0</span><span>+ New</span><span>Edit Page</span><span>Edit with PageBuilder</span><span>Builder Debugger</span><span>Clear Cache</span>
  <span class="right">Howdy, admin</span>
</div>

<div class="abs hero" role="img" aria-label="Photo of two boxers trading punches in a ring under dark arena lights"></div>

<div class="abs topline">
  <div class="abs ask"><span class="dot"></span>Want To Learn More About The Program?</div>
  <div class="abs social" aria-label="Social links"><span class="sq"></span><span class="sq"></span><span class="sq"></span></div>
</div>

<div class="abs brand header-brand"><span class="mark"></span>Punch For Purpose</div>

<nav class="abs nav"><span>HOME</span><span>ABOUT THE PROGRAM</span><span>MEET THE TEAM</span><span>PAST FIGHTERS</span><span>CONTACT</span></nav>
<div class="abs join">JOIN NOW</div>

<div class="abs hero-kicker">CONTACT US</div>
<h1 class="abs hero-title">WE WOULD BE HAPPY TO<br>ASSIST YOU</h1>
<div class="abs crumbs"><span>HOME</span><span class="sep">›</span><span>CONTACT US</span></div>

<svg class="abs" style="left:0;top:570px" width="1200" height="190" viewBox="0 0 1200 190">
  <path d="M0,15 Q600,260 1200,5 L1200,190 L0,190Z" fill="var(--pink)"/>
  <path d="M0,35 Q600,310 1200,20 L1200,190 L0,190Z" fill="var(--white)"/>
</svg>

<div class="abs map big-map" role="img" aria-label="Map of the gym location and surrounding city"></div>

<section class="abs contact-info">
  <div class="label">Contact</div>
  <h2>We Would Be Happy To Assist You</h2>
  <p>14 Canvas Lane, Harbour City, QLD</p>
  <p>hello@punchforpurpose-example.com.au</p>
  <p>+61-400-555-019</p>
  <div class="icons" aria-label="Social links"><span><i class="sq" style="width:10px;height:10px"></i></span><span><i class="sq" style="width:10px;height:10px"></i></span><span><i class="sq" style="width:10px;height:10px"></i></span></div>
</section>

<section class="abs contact-form">
  <h3>Send Us a Message</h3>
  <div class="field">Name</div>
  <div class="field">Email</div>
  <div class="field msg">Message</div>
  <div class="send">Send</div>
</section>

<div class="abs cta" role="img" aria-label="Photo of a boxing bout seen from ringside"></div>
<svg class="abs" style="left:0;top:1555px" width="1200" height="220" viewBox="0 0 1200 220">
  <path d="M0,0 L1200,0 L1200,50 Q600,330 0,40Z" fill="var(--pink)"/>
  <path d="M0,0 L1200,0 L1200,35 Q600,260 0,30Z" fill="var(--white)"/>
</svg>
<div class="abs cta-kicker">GOT ANY QUESTION</div>
<h2 class="abs cta-title">DROP US A LINE AND KEEP IN<br>TOUCH</h2>
<div class="abs cta-btn">CONTACT US</div>

<footer class="abs footer"></footer>
<div class="abs brand footer-brand"><span class="mark"></span>Punch For Purpose</div>
<div class="abs links">
  <h4>QUICK LINKS</h4>
  <ul><li>About Us</li><li>Programs</li><li>Previous Fighters</li><li>Team</li><li>Contact</li></ul>
</div>
<div class="abs training">
  <h4>TRAINING</h4>
  <div class="addr">
    <svg width="12" height="16" viewBox="0 0 12 16"><path d="M6 0a6 6 0 0 0-6 6c0 4.5 6 10 6 10s6-5.5 6-10a6 6 0 0 0-6-6zm0 8.5A2.5 2.5 0 1 1 6 3.5a2.5 2.5 0 0 1 0 5z" fill="var(--pink)"/></svg>
    <span>Corner Post Boxing – 21 Riverbend Road, Eastvale</span>
  </div>
</div>
<div class="abs map small-map" role="img" aria-label="Small map of the training gym location"></div>
<div class="abs rule"></div>
<div class="abs copy">Copyright © Punch For Purpose 2023 All Right Reserved.</div>
<div class="abs foot-social" aria-label="Social links"><span><i></i></span><span><i></i></span><span><i></i></span></div>

</body>
</html>
```